Business Card Design for Flood Rescue 360 - Property Restoration Professionals

I need a business card designed for Flood Rescue 360. We are a full-service property restoration solution. Providing water, fire, smoke & storm restoration as well as mold remediation and full remodel or reconstruction to homes and businesses across Dallas-Fort Worth, TX.
Target Market(s)
home and business owners with insurance covered property damage from water, fire or storm related damage
Industry/Entity Type
property restoration
Contact Information for Business Card
Marcus Pelley General Manager Cell: 214-555-0193 Office: 469-555-0148 email: Marcus@FloodRescue360.example services: Water, Fire, Mold, Reconstruction Tagline: Urgency for Your Water Emergency!
Look and feel
Each slider illustrates characteristics of the customer's brand and the style your logo design should communicate.

```html
<!DOCTYPE html>
<html lang="en">
<head>
<meta charset="utf-8">
<title>Flood Rescue 360 – Business Card</title>
<link href="https://fonts.googleapis.com/css2?family=Montserrat:wght@400;500;800&display=swap" rel="stylesheet">
<style>
  :root{
    --bg:#4a4a4a;
    --card:#161616;
    --accent:#12b2e6;
    --text:#f2f2f2;
    --muted:#8a8a8a;
    --emboss:#2a2a2a;
  }
  *{margin:0;padding:0;box-sizing:border-box}
  html,body{width:1200px;height:801px;overflow:hidden}
  body{
    background:var(--bg);
    font-family:"Montserrat",sans-serif;
    display:flex;align-items:center;justify-content:center;gap:40px;
  }
  .card{
    position:relative;width:550px;height:314px;
    background:var(--card);
    border-bottom:3px solid var(--accent);
    box-shadow:0 14px 30px rgba(0,0,0,.35);
    overflow:hidden;
  }
  .brand{
    position:absolute;left:30px;top:30px;
    display:flex;align-items:center;gap:10px;
    color:var(--accent);font-weight:800;font-size:24px;line-height:1;
    text-transform:uppercase;letter-spacing:.5px;
  }
  .brand-dot{width:20px;height:20px;border-radius:50%;background:var(--accent)}
  .person{position:absolute;left:30px;top:86px}
  .person-name{color:var(--accent);font-weight:800;font-size:27px;line-height:1.1}
  .person-title{color:var(--text);font-size:15px;margin-top:4px}
  .tagline{position:absolute;left:30px;top:160px;color:var(--text);font-size:14px}
  .contacts{position:absolute;left:30px;top:196px;list-style:none}
  .contacts li{display:flex;align-items:center;gap:8px;color:var(--text);font-size:14px;line-height:24px}
  .contacts svg{width:14px;height:14px;flex:none}
  .services{position:absolute;right:30px;top:34px;text-align:right}
  .services-heading{color:var(--accent);font-weight:800;font-size:24px;letter-spacing:.5px;margin-bottom:8px}
  .services ul{list-style:none}
  .services li{
    color:var(--text);font-size:15px;line-height:25px;
    display:flex;align-items:center;justify-content:flex-end;gap:7px;
  }
  .services li::after{
    content:"";width:7px;height:7px;border-radius:50%;
    border:1.5px solid var(--accent);
  }
  .card-back{display:flex;align-items:center;justify-content:center}
  .back-mark{
    display:flex;align-items:center;gap:14px;
    color:var(--muted);font-weight:800;font-size:30px;text-transform:uppercase;letter-spacing:1px;
  }
  .back-mark .brand-dot{width:26px;height:26px;background:var(--muted)}
</style>
</head>
<body>
  <section class="card card-front" aria-label="Business card front">
    <div class="brand"><span>Flood Rescue 360</span><span class="brand-dot"></span></div>

    <div class="person">
      <p class="person-name">Marcus Pelley</p>
      <p class="person-title">General Manager</p>
    </div>

    <p class="tagline">Urgency for Your Water Emergency!</p>

    <ul class="contacts">
      <li>
        <svg viewBox="0 0 14 14" fill="none" stroke="var(--accent)" stroke-width="1.5"><rect x="3.5" y="1" width="7" height="12" rx="1.2"/><line x1="6" y1="11" x2="8" y2="11"/></svg>
        214-555-0193
      </li>
      <li>
        <svg viewBox="0 0 14 14" fill="var(--accent)"><path d="M1 5c0-2 3-3 6-3s6 1 6 3l-2.5 1-1-1.5h-5l-1 1.5z"/><rect x="3" y="8" width="8" height="5" rx="1"/></svg>
        469-555-0148
      </li>
      <li>
        <svg viewBox="0 0 14 14" fill="none" stroke="var(--accent)" stroke-width="1.5"><rect x="1" y="3" width="12" height="8" rx="1"/><path d="M1 3l6 5 6-5"/></svg>
        Marcus@FloodRescue360.example
      </li>
      <li>
        <svg viewBox="0 0 14 14" fill="none" stroke="var(--accent)" stroke-width="1.5"><circle cx="7" cy="7" r="5.7"/><ellipse cx="7" cy="7" rx="2.5" ry="5.7"/><line x1="1.3" y1="7" x2="12.7" y2="7"/></svg>
        FloodRescue360.example
      </li>
    </ul>

    <div class="services">
      <h2 class="services-heading">SERVICES</h2>
      <ul>
        <li>Water</li>
        <li>Fire</li>
        <li>Mold</li>
        <li>Reconstruction</li>
      </ul>
    </div>
  </section>

  <section class="card card-back" aria-label="Business card back">
    <div class="back-mark"><span class="brand-dot"></span><span>Flood Rescue 360</span></div>
  </section>
</body>
</html>
```